Design a business card
Business name: Harbourline Growth Advisory
Improving Business Profitibility

- An Overview of the Business & Service:

Business Performance Consulting

- The Target Market: Small to medium-sized business

- Design Specifics:
White card, blue ink, moon eclipse

No Logo

Target Market(s)

Small to medium-sized business

Font styles to use
Sans Serif

```html
<!DOCTYPE html>
<html lang="en">
<head>
<meta charset="utf-8">
<title>Harbourline Growth Advisory – Business Card</title>
<link rel="stylesheet" href="https://fonts.googleapis.com/css2?family=Bebas+Neue&family=Open+Sans:wght@400&family=Oswald:wght@400&display=swap">
<style>
  :root {
    --backdrop: #9a9a9a;
    --card-white: #ffffff;
    --card-black: #000000;
    --ink-blue: #2c67ad;
    --ink-dark: #222222;
    --rule-grey: #b5b5b5;
    --rule-dark: #262626;
    --tagline-grey: #a6a6a6;
    --moon-tone: #b4461c;
    --moon-tone-deep: #9a3814;
  }
  html, body {
    margin: 0;
    width: 1200px;
    height: 900px;
    overflow: hidden;
    background: var(--backdrop);
  }
  .canvas {
    position: relative;
    width: 1200px;
    height: 900px;
  }
  .card {
    position: absolute;
    width: 477px;
    height: 293px;
    box-shadow: 4px 4px 6px rgba(0, 0, 0, 0.55);
    overflow: hidden;
  }
  /* Front */
  .card-front {
    left: 120px;
    top: 275px;
    background: var(--card-white);
    border-radius: 0 52px 0 52px;
  }
  .company {
    position: absolute;
    right: 33px;
    top: 62px;
    width: 290px;
    margin: 0;
    font-weight: 400;
    font-family: "Bebas Neue", sans-serif;
    color: var(--ink-blue);
    text-align: right;
    white-space: nowrap;
  }
  .company-line1 {
    display: block;
    font-size: 37px;
    line-height: 38px;
    letter-spacing: 0.2px;
  }
  .company-line2 {
    display: flex;
    align-items: center;
    gap: 8px;
    font-size: 33px;
    line-height: 34px;
  }
  .company-line2::before,
  .company-line2::after {
    content: "";
    flex: 1;
    height: 3px;
    background: var(--ink-blue);
  }
  .person-name {
    position: absolute;
    left: 30px;
    top: 156px;
    margin: 0;
    font-family: "Bebas Neue", sans-serif;
    font-size: 22px;
    font-weight: 400;
    color: var(--ink-blue);
  }
  .person-role {
    position: absolute;
    left: 29px;
    top: 180px;
    margin: 0;
    font-family: "Open Sans", sans-serif;
    font-size: 12.5px;
    color: var(--ink-dark);
  }
  .name-rule {
    position: absolute;
    left: 148px;
    top: 189px;
    width: 296px;
    height: 1px;
    background: var(--rule-grey);
  }
  .address {
    position: absolute;
    left: 31px;
    top: 234px;
    font-family: "Open Sans", sans-serif;
    font-size: 12.5px;
    line-height: 17px;
    color: var(--ink-dark);
    font-style: normal;
  }
  .contacts {
    position: absolute;
    right: 33px;
    top: 199px;
    margin: 0;
    padding: 0;
    list-style: none;
    font-family: "Open Sans", sans-serif;
    font-size: 12.5px;
    line-height: 17.3px;
    color: var(--ink-dark);
    text-align: right;
  }
  .contacts li {
    display: flex;
    justify-content: flex-end;
    align-items: center;
    gap: 1px;
  }
  .contacts svg {
    width: 11px;
    height: 11px;
    fill: var(--ink-blue);
  }
  /* Back */
  .card-back {
    left: 607px;
    top: 274px;
    background: var(--card-black);
    border-radius: 52px 0 52px 0;
  }
  .eclipse-moon {
    position: absolute;
    left: 179px;
    top: 69px;
    width: 124px;
    height: 124px;
    border-radius: 50%;
    background: linear-gradient(180deg, var(--moon-tone) 0%, var(--moon-tone-deep) 100%);
  }
  .back-rule {
    position: absolute;
    left: 66px;
    top: 223px;
    width: 343px;
    height: 1px;
    background: var(--rule-dark);
  }
  .tagline {
    position: absolute;
    left: 0;
    right: 0;
    top: 243px;
    margin: 0;
    font-family: "Oswald", sans-serif;
    font-size: 14.5px;
    letter-spacing: 0.8px;
    color: var(--tagline-grey);
    text-align: center;
    text-transform: uppercase;
  }
</style>
</head>
<body>
<main class="canvas">
  <section class="card card-front" aria-label="Business card front">
    <h1 class="company">
      <span class="company-line1">HARBOURLINE GROWTH</span>
      <span class="company-line2">ADVISORY</span>
    </h1>
    <h2 class="person-name">DESMOND R AKERLY</h2>
    <p class="person-role">Managing Director</p>
    <div class="name-rule"></div>
    <address class="address">12345, Address Goes Here<br>Country Name, 123456</address>
    <ul class="contacts">
      <li>044-123 456 789
        <svg viewBox="0 0 12 12" aria-hidden="true"><path d="M1 5c0-2 2-3 5-3s5 1 5 3l-2 .5-.5-1.5h-5L3 5.5zM3 6h6l1.5 4h-9z"/></svg>
      </li>
      <li>044-123 456 789
        <svg viewBox="0 0 12 12" aria-hidden="true"><path d="M3.5 0.5h5a1 1 0 0 1 1 1v9a1 1 0 0 1-1 1h-5a1 1 0 0 1-1-1v-9a1 1 0 0 1 1-1zm.3 1.5v7h4.4V2z"/></svg>
      </li>
      <li>info@harbourline.com
        <svg viewBox="0 0 12 12" aria-hidden="true"><path d="M0.5 2.5h11v7h-11zM1.5 3.3 6 6.6l4.5-3.3z" fill-rule="evenodd"/></svg>
      </li>
      <li>www.harbourline.com
        <svg viewBox="0 0 12 12" aria-hidden="true"><circle cx="6" cy="6" r="5.5"/><path d="M3 4c1-1 2 0 2 1s-1 1 0 2 1 2 0 3M8 2c-1 1 0 2 1 2s1.5 1 1 2" stroke="#fff" stroke-width="0.8" fill="none"/></svg>
      </li>
    </ul>
  </section>

  <section class="card card-back" aria-label="Business card back">
    <div class="eclipse-moon" role="img" aria-label="Photograph of a red lunar eclipse moon"></div>
    <div class="back-rule"></div>
    <p class="tagline">Improving Business Profitibility</p>
  </section>
</main>
</body>
</html>
```